Tech business card design

We need an amazing business card design for our new business 'Pexla' a marketing tech startup based in Sydney, Australia. We provide an online marketplace for businesses to search and buy advertising media, connect with service providers and learn more about marketing. We wish to communicate 'cool tech', reliability and professionalism and design based around our logo.

Target Market(s)

Business Owners

Contact Information for Business Card

Name
Position
Email Address
Website
Phone Number

Font styles to use
Other font styles liked:
• Avenir & Avenir Next

Colors

Designer to choose colors to be used in the design.

```html
<!DOCTYPE html>
<html lang="en">
<head>
<meta charset="utf-8">
<title>Pexla business card</title>
<link rel="stylesheet" href="https://fonts.googleapis.com/css2?family=Open+Sans:wght@400;700;800&display=swap">
<style>
  :root {
    --backdrop: #e1dedd;
    --card-white: #ffffff;
    --card-tint: #dfdfe9;
    --navy: #22274a;
    --wordmark: #141a3b;
    --ink: #2a2e4c;
    --ink-dark: #222222;
    --edge: #6d6d6d;
  }
  html, body {
    margin: 0;
    padding: 0;
    overflow: hidden;
    background: var(--backdrop);
  }
  .canvas {
    position: relative;
    width: 975px;
    height: 1200px;
    overflow: hidden;
    background: var(--backdrop);
    font-family: "Open Sans", Arial, sans-serif;
  }
  .card {
    position: absolute;
    left: 58px;
    width: 859px;
    height: 491px;
    display: block;
  }
  .card-front { top: 88px; }
  .card-back { top: 634px; }
  .card-base { fill: var(--card-white); stroke: var(--edge); stroke-width: 1.2; }
  .tint { fill: var(--card-tint); }
  .chevron { fill: var(--navy); }
  .wordmark {
    font-family: "Open Sans", Arial, sans-serif;
    font-weight: 800;
    fill: var(--wordmark);
    letter-spacing: -4px;
  }
  .name { font-weight: 700; font-size: 31px; fill: var(--ink-dark); }
  .role { font-weight: 400; font-size: 28px; fill: var(--ink-dark); }
  .contact { font-weight: 400; font-size: 24px; fill: var(--ink); }
  .address { font-weight: 400; font-size: 25px; fill: var(--ink); }
  .site { font-weight: 400; font-size: 31px; fill: var(--ink); letter-spacing: 4px; }
  .icon-line { fill: none; stroke: var(--ink); stroke-width: 2; }
  .icon-fill { fill: var(--ink); }
</style>
</head>
<body>
<div class="canvas">

  <svg class="card card-front" viewBox="0 0 1050 600" aria-label="Business card front">
    <rect class="card-base" x="0.6" y="0.6" width="1048.8" height="598.8"/>
    <polygon class="tint" points="384,0 1050,0 1050,600 384,600 597,283"/>
    <polygon class="chevron" points="314,0 380,0 566,283 358,600 314,600 529,283"/>

    <text class="wordmark" x="36" y="335" font-size="150">pexla</text>

    <g text-anchor="end">
      <text class="name" x="926" y="204">ALEX MORAN</text>
      <text class="role" x="926" y="245">Position</text>
      <text class="contact" x="891" y="297">012-345-6789</text>
      <text class="contact" x="891" y="337">info@pexla.com</text>
      <text class="contact" x="891" y="377">www.pexla.com</text>
      <text class="address" x="926" y="432">Street name City Name,</text>
      <text class="address" x="926" y="467">Zipcode,012345</text>
    </g>

    <g class="icon-phone" transform="translate(913,289)">
      <circle class="icon-line" r="12"/>
      <path class="icon-fill" d="M-6,-6 l4,-1 l3,5 l-3,2 q2,4 5,6 l2,-3 l5,3 l-1,4 q-4,3 -10,-2 q-6,-6 -5,-14 z"/>
    </g>
    <g class="icon-mail" transform="translate(913,329)">
      <rect class="icon-fill" x="-13" y="-9" width="26" height="18"/>
      <path d="M-13,-9 L0,2 L13,-9 M-13,9 L-3,0 M13,9 L3,0" fill="none" stroke="#dfdfe9" stroke-width="2"/>
    </g>
    <g class="icon-globe" transform="translate(913,370)">
      <circle class="icon-line" r="12"/>
      <ellipse class="icon-line" rx="5" ry="12" stroke-width="1.5"/>
      <path class="icon-line" stroke-width="1.5" d="M-12,0 H12 M-10,-6 H10 M-10,6 H10"/>
    </g>
  </svg>

  <svg class="card card-back" viewBox="0 0 1050 600" aria-label="Business card back">
    <rect class="card-base" x="0.6" y="0.6" width="1048.8" height="598.8"/>
    <polygon class="tint" points="0,28 174,293 0,570"/>
    <polygon class="chevron" points="14,0 69,0 259,293 74,600 17,600 199,293"/>
    <polygon class="tint" points="1050,28 874,293 1050,570"/>
    <polygon class="chevron" points="984,0 1039,0 851,293 1039,600 984,600 791,293"/>

    <text class="wordmark" x="524" y="370" font-size="175" text-anchor="middle">pexla</text>
    <text class="site" x="524" y="546" text-anchor="middle">www.pexla.com</text>
  </svg>

</div>
</body>
</html>
```